kolvarin.link kolvarin.space kolvarin.press website

The website is named KOLVARIN and it will have 3 domain names. kolvarin.link, press, space.
I'd like it to be viewed on Pads, pcs and phones.

page menu:

kolvarin.link(start page): presentation of company. (creative, design, app, new product innovation.)
Here we'll need sosial media icons: plimber, vendoloop, mirtavel, trelvanet. (light but some 'fruity' colors)

kolvarin.press: blog. It will be a 75% picture blog > rest will be text. I need to be able to resize pictures and shape columns to picture size. (light but some 'fruity' colors)

kolvarin.space : the fun part of this web design, however, on entering the page I'd like a non-disclosure agreement where viewer simply click "yes, I agree" after filling out contact info. (check attached document)
We will have space here for uploading PDF files viewers can download. There is also a blog space here to tell in brief about the PDF file. (maybe a space/sci-fi theme her e.g spacechimp, Laika the space dog?)

I will attach the logo here I want you to use > and develop for the .space .press webpage. The logo i uploaded is for the .link page.

Target Market(s)

venture capitalists

Number of Pages Required

3 page

Requirements
Must have
• a few 'fruity colors' but mostly white and grey

```html
<!DOCTYPE html>
<html lang="en">
<head>
<meta charset="utf-8">
<title>Kolvarin</title>
<link href="https://fonts.googleapis.com/css2?family=Rajdhani:wght@500;600&family=Lato:wght@400;700&display=swap" rel="stylesheet">
<style>
:root{
  --red:#c95d52;
  --blue:#67a6cc;
  --green:#66a95f;
  --purple:#8556be;
  --dark:#2c2c2c;
  --darker:#1e1e1e;
  --paper:#f3f3f3;
  --band:#e8e8e8;
  --text:#3a3a3a;
  --muted:#555;
}
*{box-sizing:border-box;margin:0;padding:0}
html,body{width:915px;height:1200px;overflow:hidden}
body{position:relative;background:var(--paper);font-family:"Lato",sans-serif;color:var(--text)}
.abs{position:absolute}

/* header */
.topstrip{left:0;top:0;width:915px;height:31px;background:linear-gradient(#dcdcdc,#cfcfcf)}
.navbar{left:0;top:31px;width:915px;height:35px;background:var(--red)}
.navline{left:0;top:66px;width:915px;height:7px;background:#d9d9d9}
.menu{left:131px;top:31px;height:35px;display:flex;align-items:center;font-family:"Rajdhani",sans-serif;font-weight:500;font-size:12px;color:#fff}
.menu a{color:#fff;text-decoration:none;padding:0 14px;position:relative;height:35px;display:flex;align-items:center}
.menu a+a{border-left:1px solid rgba(255,255,255,.35);height:14px}
.menu a.active::before,.menu a.active::after{content:"";position:absolute;left:0;right:0;height:3px;background:#7cc36f;border-radius:2px}
.menu a.active::before{top:-3px}.menu a.active::after{bottom:-3px}
.contact-top{top:31px;height:35px;display:flex;align-items:center;gap:7px;color:#fff;font-family:"Rajdhani",sans-serif;font-weight:500;font-size:12.5px}
.ring{width:23px;height:23px;border:1.5px solid #fff;border-radius:50%;display:flex;align-items:center;justify-content:center}
.logo{left:381px;top:-46px;width:152px;height:152px;border-radius:50%;background:#fbfbf8;box-shadow:0 4px 10px rgba(0,0,0,.25);display:flex;align-items:flex-end;justify-content:center;padding-bottom:30px}
.logo span{font-family:"Rajdhani",sans-serif;font-weight:600;font-size:20px;color:var(--dark);letter-spacing:1px}

/* hero */
.hero{left:0;top:73px;width:915px;height:357px;background:linear-gradient(180deg,#bdbab5 0%,#d6d3ce 40%,#a6a39e 100%)}
.caption{left:0;top:369px;width:915px;height:61px;background:rgba(40,40,40,.82)}
.caption h1{position:absolute;left:122px;top:14px;font-family:"Rajdhani",sans-serif;font-weight:500;font-size:24px;color:#fff}
.dots{position:absolute;left:756px;top:26px;display:flex;gap:4px}
.dots i{width:9px;height:9px;border-radius:50%;background:#fff}
.dots i:first-child{background:var(--red)}

/* welcome */
.welcome{left:0;top:430px;width:915px;height:172px;text-align:center}
.welcome h2{margin-top:32px;font-family:"Rajdhani",sans-serif;font-weight:500;font-size:19px;color:#555}
.welcome h2 em{font-style:normal;color:var(--red)}
.welcome p{width:672px;margin:25px auto 0;font-size:9px;line-height:14.6px;color:var(--text)}
.welcome p a{color:#6cb763}

/* services */
.services{left:0;top:602px;width:915px;height:232px;background:var(--band);border-top:1px solid #dedede;border-bottom:1px solid #dedede}
.tile{top:68px;width:155px;height:112px;color:#fff;text-align:center;font-family:"Rajdhani",sans-serif;font-weight:500;font-size:14.5px;line-height:17px}
.tile .icon{position:absolute;left:44px;top:-34px;width:67px;height:67px;border-radius:50%;background:#fff;border:3px solid #eee;display:flex;align-items:center;justify-content:center}
.tile .label{position:absolute;left:0;right:0;top:52px}
.tile .plus{position:absolute;left:66px;bottom:-11px;width:23px;height:22px;background:var(--dark);color:#fff;font-size:16px;line-height:22px;font-family:"Lato",sans-serif;font-weight:700}
.creative{left:122px;background:var(--blue)}
.design{left:294px;background:var(--red)}
.app{left:466px;background:var(--green)}
.innovation{left:637px;background:var(--purple)}
.innovation .label{top:53px}

/* posts */
.post{top:894px;width:322px;height:140px;background:#fff;box-shadow:0 1px 3px rgba(0,0,0,.2)}
.post .photo{position:absolute;left:0;top:0;width:145px;height:140px}
.post h3{position:absolute;left:159px;top:17px;width:110px;font-size:9.5px;line-height:14px;font-weight:700;color:#222}
.post hr{position:absolute;left:156px;top:50px;width:155px;border:0;border-top:1px solid #ddd}
.post p{position:absolute;left:156px;top:60px;width:158px;font-size:8.8px;line-height:14.4px;color:#444}
.post a{position:absolute;left:157px;top:117px;font-size:7.5px;font-weight:700;color:#6cb763;text-decoration:none}
.date{position:absolute;left:267px;top:-20px;width:42px;height:43px;background:var(--green);color:#fff;text-align:center;border-radius:2px}
.date b{display:block;font-family:"Rajdhani",sans-serif;font-weight:600;font-size:18px;line-height:22px;margin-top:2px}
.date small{display:block;font-size:8px;font-weight:700}

/* footer */
.footnav{left:0;top:1094px;width:915px;height:40px;background:var(--red);display:flex;justify-content:center;align-items:center;gap:14px;font-size:9.5px;color:#fff;letter-spacing:.3px}
.footnav .star{font-size:8px;color:var(--dark)}
.footnav a:first-child{color:var(--dark)}
.contactbar{left:0;top:1134px;width:915px;height:38px;background:var(--dark);color:#ddd;font-size:8.5px}
.contactbar .item{position:absolute;top:0;height:38px;display:flex;align-items:center;gap:6px}
.mailring{width:26px;height:26px;border-radius:50%;background:#d4d4d4;display:flex;align-items:center;justify-content:center}
.subscribe{position:absolute;left:640px;top:7px;width:152px;height:22px;display:flex}
.subscribe span{flex:1;background:#3a3a3a;color:#bbb;font-size:7.5px;padding-left:7px;line-height:22px}
.subscribe b{width:23px;background:#6cb763;color:#fff;font-size:9px;text-align:center;line-height:22px}
.copyright{left:0;top:1172px;width:915px;height:28px;background:var(--darker)}
.copyright p{position:absolute;left:124px;top:9px;font-size:8px;font-weight:700;color:#eee}
.social{position:absolute;left:704px;top:4px;display:flex;gap:5px}
.social i{width:19px;height:19px;border-radius:50%;background:#fff}
</style>
</head>
<body>

<header>
  <div class="abs topstrip"></div>
  <div class="abs navbar"></div>
  <div class="abs navline"></div>
  <nav class="abs menu">
    <a class="active" href="#">Home</a>
    <a href="#">About</a>
    <a href="#">Press</a>
    <a href="#">Space</a>
  </nav>
  <div class="abs contact-top" style="left:555px">
    <span class="ring"><svg width="11" height="9" viewBox="0 0 11 9"><rect x=".5" y=".5" width="10" height="8" rx="1" fill="none" stroke="#fff"/><path d="M1 1l4.5 4L10 1" fill="none" stroke="#fff"/></svg></span>
    info@kolvarin.com
  </div>
  <div class="abs contact-top" style="left:684px">
    <span class="ring"><svg width="10" height="10" viewBox="0 0 10 10"><path d="M2 1l2 2-1 1.3c.6 1.3 1.5 2.2 2.7 2.7L7 6l2 2-1.2 1.3C4.5 9 1 5.5.7 2.2z" fill="#fff"/></svg></span>
    +1 555 0142 776
  </div>
  <div class="abs logo"><span>KOLVARIN</span></div>
</header>

<section class="abs hero" role="img" aria-label="Crumpled paper balls in blue, red, green, purple and coral lined up on a floor, a yellow one forming a light bulb with drawn arrows"></section>
<div class="abs caption">
  <h1>Share your creativity to world</h1>
  <div class="dots"><i></i><i></i><i></i></div>
</div>

<section class="abs welcome">
  <h2>Welcome to <em>Brightmere</em></h2>
  <p>Sed ut perspiciatis unde omnis iste natus error sit voluptatem accusantium doloremque laudantium, totam rem aperiam, eaque ipsa quae ab illo inventore veritatis et quasi architecto beatae vitae dicta sunt explicabo. Nemo enim ipsam voluptatem quia voluptas sit aspernatur aut odit aut voluptas sit aspernatur aut odit aut fugit. Sed ut perspiciatis unde omnis iste natus error sit voluptatem accusantium doloremque laudantium, totam rem aperiam, eaque ipsa quae ab illo inventore veritatis et quasi architecto beatae vitae dicta sunt explicabo. Nemo enim ipsam voluptatem quia voluptas sit aspernatur . <a href="#">More</a></p>
</section>

<section class="abs services">
  <div class="abs tile creative">
    <div class="icon"><svg width="34" height="34" viewBox="0 0 34 34"><path d="M15 3c-7 0-11 5-11 10 0 3 1 5 3 7v11h12v-5h5v-7l3-1-3-5c0-6-4-10-9-10z" fill="var(--blue)"/><circle cx="13" cy="12" r="3.5" fill="none" stroke="#fff" stroke-width="1.6"/><circle cx="19" cy="17" r="2.5" fill="none" stroke="#fff" stroke-width="1.4"/></svg></div>
    <div class="label">CREATIVE</div><div class="plus">+</div>
  </div>
  <div class="abs tile design">
    <div class="icon"><svg width="34" height="34" viewBox="0 0 34 34" fill="none" stroke="var(--red)" stroke-width="1.6"><rect x="13" y="2" width="8" height="30" transform="rotate(45 17 17)"/><rect x="13" y="4" width="7" height="26" transform="rotate(-45 17 17)"/></svg></div>
    <div class="label">DESIGN</div><div class="plus">+</div>
  </div>
  <div class="abs tile app">
    <div class="icon"><svg width="34" height="34" viewBox="0 0 34 34" fill="none" stroke="var(--green)" stroke-width="1.6"><rect x="8" y="3" width="14" height="27" rx="2"/><line x1="8" y1="25" x2="22" y2="25"/><circle cx="22" cy="15" r="5" fill="#fff"/><circle cx="22" cy="15" r="2"/></svg></div>
    <div class="label">APP</div><div class="plus">+</div>
  </div>
  <div class="abs tile innovation">
    <div class="icon"><svg width="34" height="34" viewBox="0 0 34 34" fill="none" stroke="var(--purple)" stroke-width="1.6"><path d="M17 8a7 7 0 0 0-4 12.5V24h8v-3.5A7 7 0 0 0 17 8z"/><line x1="14" y1="27" x2="20" y2="27"/><path d="M17 2v3M6 6l2 2M28 6l-2 2M3 15h3M31 15h-3"/></svg></div>
    <div class="label">NEW PRODUCT<br>INNOVATION</div><div class="plus">+</div>
  </div>
</section>

<article class="abs post" style="left:124px">
  <div class="photo" role="img" aria-label="Tree illustration with colourful paint splash foliage" style="background:radial-gradient(circle at 50% 40%,#e8527a 0%,#f2a23a 30%,#7fb94a 50%,#fff 72%)"></div>
  <div class="date"><b>06</b><small>April</small></div>
  <h3>Simply dummy text of the printing</h3>
  <hr>
  <p>Lorem Ipsum is simply dummy text of the printing and typesetting indus text ever since the 1500s,</p>
  <a href="#">Read More &gt;&gt;</a>
</article>

<article class="abs post" style="left:470px">
  <div class="photo" role="img" aria-label="Yellow crumpled paper light bulb with the word Creative on white" style="background:radial-gradient(circle at 30% 45%,#f3dd3a 0%,#f7ef9c 18%,#f5f5f3 40%,#ecebe7 100%)"></div>
  <div class="date"><b>04</b><small>April</small></div>
  <h3>Simply dummy text of the printing</h3>
  <hr>
  <p>Lorem Ipsum is simply dummy text of the printing and typesetting indus text ever since the 1500s,</p>
  <a href="#">Read More &gt;&gt;</a>
</article>

<footer>
  <nav class="abs footnav">
    <a>HOME</a><span class="star">★</span><a>ABOUT US</a><span class="star">★</span><a>PRESS</a><span class="star">★</span><a>SPACE</a>
  </nav>
  <div class="abs contactbar">
    <div class="item" style="left:128px"><svg width="12" height="16" viewBox="0 0 12 16"><path d="M6 0a6 6 0 0 0-6 6c0 4 6 10 6 10s6-6 6-10a6 6 0 0 0-6-6z" fill="#ddd"/><circle cx="6" cy="6" r="2.2" fill="#2c2c2c"/></svg>Lorem ipsum dolor sit amet, adipiscing elit</div>
    <div class="item" style="left:346px;font-size:10.5px"><svg width="10" height="14" viewBox="0 0 10 14"><path d="M2 1l2.5 2.5-1.2 1.5c.5 2 1.5 3.5 3 4.5L8 8.5l2 2.5-1.5 2C4 12 1 7 1 2z" fill="#ddd"/></svg>+1 555 0142 776</div>
    <div class="item" style="left:477px"><span style="font-size:17px">@</span>info@kolvarin.com</div>
    <div class="item" style="left:610px"><span class="mailring"><svg width="13" height="10" viewBox="0 0 13 10"><rect width="13" height="10" rx="1" fill="#2c2c2c"/><path d="M1 1l5.5 4.5L12 1" fill="none" stroke="#d4d4d4"/></svg></span></div>
    <div class="subscribe"><span>Enter Email</span><b>GO</b></div>
  </div>
  <div class="abs copyright">
    <p>Copyright 2016  Kolvarin. All rights reserved.</p>
    <div class="social">
      <i aria-label="mirtavel"></i><i aria-label="plimber"></i><i aria-label="vendoloop"></i><i aria-label="trelvanet"></i>
    </div>
  </div>
</footer>

</body>
</html>
```